Business card for medical clinic

I need an upmarket, modern medical/health business card for my clinic

Contact Information for Business Card

name, address, email, qr code

```html
<!DOCTYPE html>
<html lang="en">
<head>
<meta charset="utf-8">
<title>Calder Health Partners – Business Card</title>
<link href="https://fonts.googleapis.com/css2?family=Cinzel:wght@500&family=Arimo:wght@400&display=swap" rel="stylesheet">
<style>
  :root {
    --stage: #3d3d3d;
    --paper: #ffffff;
    --rule-grey: #9a9ea3;
    --brand-blue: #1a6fb0;
    --glow-blue: #0aa8e6;
    --mid-blue: #0b6fae;
    --deep-navy: #1c2b4d;
    --ink-light: #ffffff;
  }
  * { box-sizing: border-box; margin: 0; padding: 0; }
  html, body {
    width: 1200px; height: 803px; overflow: hidden;
    background: var(--stage);
  }
  .stage {
    position: relative; width: 1200px; height: 803px;
    display: flex; align-items: center; justify-content: center; gap: 60px;
  }
  .card {
    position: relative; width: 480px; height: 274px;
    border-radius: 18px; overflow: hidden;
    box-shadow: 0 14px 30px rgba(0,0,0,.45);
  }

  /* Brand placeholder: plain name in the body font */
  .brand-name {
    font-family: "Arimo", sans-serif; font-weight: 400;
    font-size: 22px; color: var(--brand-blue); white-space: nowrap;
  }

  /* Front */
  .card--front { background: var(--paper); }
  .front__top {
    position: absolute; inset: 0 0 auto 0; height: 122px;
    display: flex; align-items: center; justify-content: center;
  }
  .front__rule {
    position: absolute; left: 0; right: 0; top: 122px; height: 5px;
    background: var(--rule-grey);
  }
  .front__band {
    position: absolute; left: 0; right: 0; top: 127px; bottom: 0;
    background: radial-gradient(ellipse 60% 90% at 50% 20%, var(--glow-blue) 0%, var(--mid-blue) 45%, var(--deep-navy) 100%);
    display: flex; align-items: center; justify-content: center;
    color: var(--ink-light);
  }
  .identity {
    text-align: right; padding-right: 16px;
    font-family: "Arimo", sans-serif; font-size: 11.5px; line-height: 1.45;
  }
  .identity__name {
    font-family: "Cinzel", serif; font-weight: 500;
    font-size: 20px; letter-spacing: 1px; line-height: 1.1;
  }
  .divider { width: 1px; height: 84px; background: rgba(255,255,255,.7); }
  .contacts {
    list-style: none; padding-left: 16px;
    font-family: "Arimo", sans-serif; font-size: 11.5px; line-height: 1.65;
  }
  .contacts li { display: flex; align-items: center; gap: 7px; }
  .contacts svg { width: 11px; height: 11px; flex: none; }

  /* Back */
  .card--back {
    background: radial-gradient(ellipse 55% 70% at 45% 50%, var(--glow-blue) 0%, var(--mid-blue) 40%, var(--deep-navy) 100%);
    display: flex; align-items: center; justify-content: center;
  }
  .card--back .brand-name { color: var(--ink-light); font-size: 30px; }
</style>
</head>
<body>
<main class="stage">
  <section class="card card--front">
    <div class="front__top">
      <span class="brand-name">Calder Health Partners</span>
    </div>
    <div class="front__rule"></div>
    <div class="front__band">
      <div class="identity">
        <p class="identity__name">Daniel Reyes</p>
        <p>President</p>
        <p>1420 Alder Court</p>
        <p>Westbrook, Canada 40218</p>
      </div>
      <div class="divider"></div>
      <ul class="contacts">
        <li>
          <svg viewBox="0 0 12 12" aria-hidden="true"><path d="M2.5 1 L4.5 1 L5 3.5 L3.8 4.3 Q5 7 7.7 8.2 L8.5 7 L11 7.5 L11 9.5 Q11 11 9.5 11 Q1 10 1 2.5 Q1 1 2.5 1Z" fill="#fff"/></svg>
          555-210-4837
        </li>
        <li>
          <svg viewBox="0 0 12 12" aria-hidden="true"><rect x="3" y="0.8" width="6" height="10.4" rx="1" fill="none" stroke="#fff" stroke-width="1.2"/><circle cx="6" cy="9.5" r=".6" fill="#fff"/></svg>
          555-210-9162
        </li>
        <li>
          <svg viewBox="0 0 12 12" aria-hidden="true"><rect x="0.5" y="2.5" width="11" height="7.5" fill="#fff"/><path d="M0.8 2.8 L6 6.8 L11.2 2.8" fill="none" stroke="#1c2b4d" stroke-width="1"/></svg>
          info@calderhealth.com
        </li>
        <li>
          <svg viewBox="0 0 12 12" aria-hidden="true"><circle cx="6" cy="6" r="5.2" fill="none" stroke="#fff" stroke-width="1.1"/><ellipse cx="6" cy="6" rx="2.2" ry="5.2" fill="none" stroke="#fff" stroke-width=".9"/><path d="M1 6 H11" stroke="#fff" stroke-width=".9"/></svg>
          www.calderhealth.com
        </li>
      </ul>
    </div>
  </section>

  <section class="card card--back">
    <span class="brand-name">Calder Health Partners</span>
  </section>
</main>
</body>
</html>
```